Update our OBGYN business card look and info

We are an OBGYN office. Our logo is nice but would like to "woman" part of the logo to be a darker color, to contrast with the flower that surrounds it. Maybe make our practice name Bloom Harbor Health more feminine. Our practice caters to women only. All providers and staff are female.

Target Market(s)

Females 16-65.

Industry/Entity Type

Business

Contact Information for Business Card

See attached upload. The ONLY CHANGE to the information is DELETE the name Paula Renwick, Midwife and REPLACE with Dora Fintelli, Midwife

Logo Text

Bloom Harbor Health Obstetrics & Gynecology

Font styles to use
Serif
Script

Colors
85cae6
0692cd
33a6d7
85abd2
f59195
eea4c8
cadf82
fac994
d3a5cc

```html
<!DOCTYPE html>
<html lang="en">
<head>
<meta charset="utf-8">
<title>Bloom Harbor Health – Business Card</title>
<link href="https://fonts.googleapis.com/css2?family=Marcellus&family=Arimo:wght@400;700&display=swap" rel="stylesheet">
<style>
  :root {
    --stage: #2a2a2a;
    --teal: #7fc3d6;
    --teal-deep: #5fb0c9;
    --paper: #f7f7f5;
    --ink: #5a5a5a;
    --ink-dark: #3f3f3f;
    --band-grey: #7a7a7a;
    --white: #ffffff;
  }
  * { margin: 0; padding: 0; box-sizing: border-box; }
  html, body { width: 1200px; height: 800px; overflow: hidden; }
  body {
    background: var(--stage);
    font-family: "Arimo", Arial, sans-serif;
    position: relative;
  }
  .card {
    position: absolute;
    width: 640px;
    height: 366px;
    left: 280px;
    overflow: hidden;
    border-radius: 3px;
  }
  .card-back { top: 22px; background: var(--teal); }
  .card-front { top: 410px; background: var(--paper); }

  .brand { position: absolute; display: flex; align-items: center; gap: 22px; }
  .brand-dot { width: 70px; height: 70px; border-radius: 50%; flex: none; }
  .brand-name {
    font-family: "Marcellus", Georgia, serif;
    font-size: 22px; letter-spacing: 0.5px; text-transform: uppercase; line-height: 1.1;
  }
  .brand-tagline { font-family: "Arimo", Arial, sans-serif; font-weight: 700; font-size: 22px; margin-top: 2px; }

  .card-back .brand { left: 140px; top: 120px; }
  .card-back .brand-dot { background: var(--white); }
  .card-back .brand-name, .card-back .brand-tagline { color: var(--white); }
  .card-back .website {
    position: absolute; left: 0; right: 0; top: 300px; text-align: center;
    color: var(--white); font-size: 15px; letter-spacing: 3px;
  }
  .card-back .website b { font-weight: 700; }

  .card-front .brand { left: 40px; top: 34px; }
  .card-front .brand-dot { background: var(--teal); }
  .card-front .brand-name { color: var(--teal); }
  .card-front .brand-tagline { color: var(--ink); }

  .contact { position: absolute; left: 52px; top: 128px; color: var(--ink-dark); font-size: 15px; line-height: 19px; font-style: normal; }
  .contact-list { list-style: none; margin-top: 6px; }
  .contact-list li { display: flex; align-items: center; gap: 8px; }
  .contact-list svg { width: 12px; height: 12px; flex: none; }

  .wave { position: absolute; left: 0; top: 0; width: 640px; height: 366px; }
  .card-front .website {
    position: absolute; left: 40px; top: 300px; color: var(--white); font-size: 16px; letter-spacing: 0.5px;
  }

  .providers {
    position: absolute; right: 44px; top: 148px; list-style: none; text-align: right;
    font-size: 16px; line-height: 20px; color: var(--ink-dark);
  }
  .providers strong { font-weight: 700; }
</style>
</head>
<body>

<section class="card card-back" aria-label="Card back">
  <div class="brand">
    <span class="brand-dot"></span>
    <div>
      <div class="brand-name">Bloom Harbor Health</div>
      <div class="brand-tagline">Obstetrics &amp; Gynecology</div>
    </div>
  </div>
  <p class="website">www.<b>bloomharbor</b>.com</p>
</section>

<section class="card card-front" aria-label="Card front">
  <svg class="wave" viewBox="0 0 640 366" aria-hidden="true">
    <path d="M0,230 C300,232 520,250 640,340 L640,366 L0,366 Z" fill="var(--teal)"/>
    <path d="M0,234 C300,242 520,272 640,362 L640,366 L0,366 Z" fill="var(--white)"/>
    <path d="M0,226 C260,236 470,300 600,366 L0,366 Z" fill="var(--band-grey)"/>
  </svg>

  <div class="brand">
    <span class="brand-dot"></span>
    <div>
      <div class="brand-name">Bloom Harbor Health</div>
      <div class="brand-tagline">Obstetrics &amp; Gynecology</div>
    </div>
  </div>

  <address class="contact">
    <div>418 Larkspur Avenue</div>
    <div>Suite 3B, Fairhaven, GA 31999</div>
    <ul class="contact-list">
      <li><svg viewBox="0 0 12 12"><path d="M3 1 L5 3.5 L4 5 C4.8 6.6 5.6 7.4 7 8 L8.5 7 L11 9 L9.5 11 C5 10.5 1.5 7 1 2.5 Z" fill="var(--teal)"/></svg>(555) 014-2286</li>
      <li><svg viewBox="0 0 12 12"><rect x="3" y="1" width="6" height="3" fill="var(--teal)"/><rect x="1" y="4.5" width="10" height="4.5" rx="1" fill="var(--teal)"/><rect x="3" y="8" width="6" height="3" fill="var(--teal-deep)"/></svg>(555) 014-7391</li>
      <li><svg viewBox="0 0 12 12"><rect x="1" y="2.5" width="10" height="7" fill="none" stroke="var(--teal)" stroke-width="1.2"/><path d="M1 2.5 L6 6.5 L11 2.5" fill="none" stroke="var(--teal)" stroke-width="1.2"/></svg>info@bloomharbor.com</li>
    </ul>
  </address>

  <ul class="providers">
    <li><strong>Marian Okafor,</strong> MD</li>
    <li><strong>Lena Castellan,</strong> MD</li>
    <li><strong>Ruth Abernay,</strong> MD</li>
    <li><strong>Dora Fintelli,</strong> Midwife</li>
    <li><strong>Celia Dunmore,</strong> Midwife</li>
  </ul>

  <p class="website">www.<strong>bloomharbor</strong>.com</p>
</section>

</body>
</html>
```